International Petrochemical business needs a web design for Clearway Desk system

We need a web design for a "Clearway Desk" system for an international petrochemical company. The web site is used internally within the company. It is hosted by an internal department which provides government permit request service for other departments.

We would like to see designs of two pages using color light blue. (home page, internal page as attached).
Home Page:
1. Header has a background image and small animation. Header on home page can be taller than the header of the internal page.
2. Layout as attached.

Internal Page:
1. Header can use the same background image as the home page and can be shorter to utilize the page for content.
2. The blue icon behind every captions represent an icon. When user move mouse over this icon, it displays the caption in Thai language as a tooltip. This icon needs to be redesign.

The final design should communicate the followings:
- Excellent service provided system in terms of time and accurary
- Rapid growth of business via building petrochemical refinery plant
Updates

For Internal Page, the blue circle behind every captions represent an icon. When mouse over this icon, a tool tip showing the caption in Thai language is shown. Please also design this icon..

There are more feedbacks from customer as followed:

1. Banner should consists of 
    1.1 "Approved" stamp on paper
    1.2 An image of Garuda. It is used on every government documents in Thailand
    1.3 Image of petrochemical plant
2. Each menu item (Home, Permit, Search, etc) should have different colors. Drop down menu will use the same color as its parent menu item.
3. Overall tone of the web page should be light blue with background of the body the web page in white
4. "New Request" button should use green color with icon on it
5. Table header of each box in the body of the page should use dark blue background with text in white

Please kindly submit your revisions.
Thank you.

Industry/Entity Type

Business

Requirements
Must have
• 1. Design for 1024x768 screen resolution
2. Use light blue theme
3. Background of header where the company logo is must have white background

```html
<!DOCTYPE html>
<html lang="en">
<head>
<meta charset="utf-8">
<title>Clearway Desk</title>
<link rel="stylesheet" href="https://fonts.googleapis.com/css2?family=Oswald:wght@300;400&family=Arimo:wght@400;700&display=swap">
<style>
:root{
  --sky-top:#1296d8;
  --sky-mid:#3fb4ea;
  --sky-pale:#d6effb;
  --navy:#1c1462;
  --head-row:#aadcef;
  --row:#cee6f0;
  --pager:#e4e4e4;
  --link:#1a8fd0;
  --label:#1a4f7a;
  --text:#333333;
  --nav-home:#12aee8;
  --nav-permits:#5f63cf;
  --nav-search:#8c9aa3;
  --nav-reports:#1aa5c3;
  --nav-admin:#73c631;
  --nav-help:#10b0ea;
  --title:#ffffff;
  --green:#72c42f;
  --green-dark:#5aab1e;
  --footer-line:#d9d2b0;
  --footer-link:#5b4b12;
  --footer-copy:#b5aa84;
  --dot-red:#e0211c;
  --dot-amber:#f0a800;
  --pager-icon:#7f94a8;
}
*{box-sizing:border-box;margin:0;padding:0}
html,body{width:1200px;height:1155px;overflow:hidden;background:#fff}
body{position:relative;font-family:"Arimo",Arial,sans-serif;color:var(--text)}
.banner{position:absolute;left:0;top:0;width:1200px;height:360px;
  background:linear-gradient(180deg,var(--sky-top) 0%,var(--sky-mid) 45%,var(--sky-pale) 82%,#fff 100%)}
.brand{position:absolute;left:30px;top:186px;display:flex;align-items:center;gap:6px;
  color:#fff;font-family:"Arimo",Arial,sans-serif;font-size:16px;font-weight:400;line-height:1}
.brand-mark{width:26px;height:26px;border-radius:50%;background:#fff}
.system-title{position:absolute;left:245px;top:188px;font-family:"Arimo",Arial,sans-serif;font-weight:700;
  font-size:44px;line-height:1;color:var(--title)}
.main-nav{position:absolute;left:18px;top:255px;height:47px;display:flex}
.main-nav a{display:flex;align-items:center;justify-content:center;color:#fff;text-decoration:none;
  font-family:"Oswald",sans-serif;font-weight:300;font-size:22px}
.nav-home{width:179px;background:var(--nav-home)}
.nav-permits{width:211px;background:var(--nav-permits)}
.nav-search{width:179px;background:var(--nav-search)}
.nav-reports{width:238px;background:var(--nav-reports)}
.nav-admin{width:173px;background:var(--nav-admin)}
.nav-help{width:182px;background:var(--nav-help)}

.panel{position:absolute;width:577px;font-size:14.5px}
.panel.wide{width:1159px}
.left{left:20px}.right{left:602px}
.panel-title{height:43px;background:var(--navy);color:#fff;font-size:17px;display:flex;align-items:center;padding-left:10px}
.grid-row{display:grid;align-items:center;padding-left:9px;border-bottom:1px solid #fff}
.grid-row.head{height:28px;background:var(--head-row);color:var(--label)}
.grid-row.data{height:29.4px;background:var(--row)}
.grid-row a{color:var(--link)}
.cols-3{grid-template-columns:164px 187px 1fr}
.cols-2{grid-template-columns:284px 1fr}
.cols-6{grid-template-columns:164px 189px 275px 165px 196px 1fr}
.pager{height:35px;background:var(--pager);display:flex;align-items:center;gap:7px;padding-left:12px}
.pager svg{display:block}
.page-no{border:1px solid #9aa;border-radius:3px;background:#fff;font-size:12px;width:26px;height:19px;
  display:flex;align-items:center;justify-content:center;color:#333}
.dot{display:inline-block;width:12px;height:12px;border-radius:50%;margin-left:6px;vertical-align:-1px}
.dot.red{background:var(--dot-red)}
.dot.amber{background:var(--dot-amber)}
.action-band{position:absolute;left:602px;top:787px;width:577px;height:54px;background:var(--green);
  display:flex;align-items:center;justify-content:center}
.action-btn{width:200px;height:44px;background:var(--green-dark);border-radius:4px;color:#fff;
  font-family:"Oswald",sans-serif;font-weight:300;font-size:25px;display:flex;align-items:center;justify-content:center}

.site-footer{position:absolute;left:18px;top:1083px;width:1161px;border-top:1px solid var(--footer-line);
  display:flex;justify-content:space-between;padding-top:18px}
.footer-links{font-size:13px;color:var(--footer-link)}
.footer-links a{color:var(--footer-link);text-decoration:none}
.footer-links span{margin:0 6px}
.copyright{font-size:13.5px;color:var(--footer-copy);margin-top:-4px}
</style>
</head>
<body>
<div class="banner" role="img" aria-label="Header artwork: approved stamp on paper, government emblem and petrochemical plant on a light blue background"></div>

<div class="brand"><span class="brand-mark"></span>Norvale Petrochemical</div>
<h1 class="system-title">Clearway Desk</h1>

<nav class="main-nav">
  <a class="nav-home" href="#">HOME</a>
  <a class="nav-permits" href="#">PERMITS</a>
  <a class="nav-search" href="#">SEARCH</a>
  <a class="nav-reports" href="#">REPORTS</a>
  <a class="nav-admin" href="#">ADMIN</a>
  <a class="nav-help" href="#">HELP</a>
</nav>

<svg width="0" height="0" style="position:absolute">
  <defs>
    <g id="pg-first"><rect x="0" y="1" width="2.5" height="11" fill="#7f94a8"/><path d="M12 1 L3.5 6.5 L12 12Z" fill="#7f94a8"/></g>
    <g id="pg-prev"><path d="M9 1 L1 6.5 L9 12Z" fill="#7f94a8"/></g>
    <g id="pg-next"><path d="M1 1 L9 6.5 L1 12Z" fill="#7f94a8"/></g>
    <g id="pg-last"><path d="M0 1 L8.5 6.5 L0 12Z" fill="#7f94a8"/><rect x="9.5" y="1" width="2.5" height="11" fill="#7f94a8"/></g>
  </defs>
</svg>

<section class="panel left" style="top:359px">
  <div class="panel-title">New Requests</div>
  <div class="grid-row head cols-3"><span>Request No.</span><span>Requested Date</span><span>Branch</span></div>
  <div class="grid-row data cols-3"><a href="#">56-0003</a><span>21/04/2013</span><span>GC1</span></div>
  <div class="grid-row data cols-3"><a href="#">56-0004</a><span>21/04/2013</span><span>GC2</span></div>
  <div class="grid-row data cols-3"></div>
  <div class="grid-row data cols-3"></div>
  <div class="pager"><svg width="12" height="13"><use href="#pg-first"/></svg><svg width="10" height="13"><use href="#pg-prev"/></svg><span class="page-no">1</span><svg width="10" height="13"><use href="#pg-next"/></svg><svg width="12" height="13"><use href="#pg-last"/></svg></div>
</section>

<section class="panel right" style="top:359px">
  <div class="panel-title">My Working Requests</div>
  <div class="grid-row head cols-3"><span>Request No.</span><span>Requested Date</span><span>Status</span></div>
  <div class="grid-row data cols-3"><a href="#">55-0200</a><span>21/04/2013</span><span>Waiting for process</span></div>
  <div class="grid-row data cols-3"><a href="#">56-0210</a><span>21/04/2013</span><span>In progress</span></div>
  <div class="grid-row data cols-3"><a href="#">55-0300</a><span>21/04/2013</span><span>Incomplete document</span></div>
  <div class="grid-row data cols-3"><a href="#">55-0301</a><span>21/04/2013</span><span>Cancel Requested</span></div>
  <div class="pager"><svg width="12" height="13"><use href="#pg-first"/></svg><svg width="10" height="13"><use href="#pg-prev"/></svg><span class="page-no">1</span><svg width="10" height="13"><use href="#pg-next"/></svg><svg width="12" height="13"><use href="#pg-last"/></svg></div>
</section>

<section class="panel wide left" style="top:604px">
  <div class="panel-title">Expiring Permits</div>
  <div class="grid-row head cols-6"><span>Permit No.</span><span>Expire Date</span><span>Permit Name</span><span>Branch</span><span>Required Time (Day)</span><span>Due Date</span></div>
  <div class="grid-row data cols-6"><a href="#">AB56001</a><span>25/03/2013</span><span>Permit Name ###10</span><span>GC1</span><span>30<i class="dot red"></i></span><span>- 40</span></div>
  <div class="grid-row data cols-6"><a href="#">BIO5502</a><span>24/03/2013</span><span>Permit Name ###20</span><span>GC2</span><span>60<i class="dot amber"></i></span><span></span></div>
  <div class="pager"><svg width="12" height="13"><use href="#pg-first"/></svg><svg width="10" height="13"><use href="#pg-prev"/></svg><span class="page-no">1</span><svg width="10" height="13"><use href="#pg-next"/></svg><svg width="12" height="13"><use href="#pg-last"/></svg></div>
</section>

<section class="panel left" style="top:787px">
  <div class="panel-title">My In Progress Request</div>
  <div class="grid-row head cols-3"><span>Request No.</span><span>Requested Date</span><span>Status</span></div>
  <div class="grid-row data cols-3"><a href="#">56-0003</a><span>21/04/2013</span><span>GC1</span></div>
  <div class="grid-row data cols-3"><a href="#">56-0004</a><span>21/04/2013</span><span>GC2</span></div>
  <div class="grid-row data cols-3"></div>
  <div class="grid-row data cols-3"></div>
  <div class="grid-row data cols-3"></div>
  <div class="pager"><svg width="12" height="13"><use href="#pg-first"/></svg><svg width="10" height="13"><use href="#pg-prev"/></svg><span class="page-no">1</span><svg width="10" height="13"><use href="#pg-next"/></svg><svg width="12" height="13"><use href="#pg-last"/></svg></div>
</section>

<div class="action-band"><a class="action-btn">NEW REQUESTS</a></div>

<section class="panel right" style="top:846px">
  <div class="panel-title">Recent Complete Requests</div>
  <div class="grid-row head cols-2"><span>Request No.</span><span>Completed Date</span></div>
  <div class="grid-row data cols-2"><a href="#">55-0200</a><span>21/04/2013</span></div>
  <div class="grid-row data cols-2"><a href="#">56-0210</a><span>21/04/2013</span></div>
  <div class="grid-row data cols-2"><a href="#">55-0300</a><span>21/04/2013</span></div>
  <div class="pager"><svg width="12" height="13"><use href="#pg-first"/></svg><svg width="10" height="13"><use href="#pg-prev"/></svg><span class="page-no">1</span><svg width="10" height="13"><use href="#pg-next"/></svg><svg width="12" height="13"><use href="#pg-last"/></svg></div>
</section>

<footer class="site-footer">
  <div class="footer-links"><a href="#">HOME</a><span>|</span><a href="#">PERMITS</a><span>|</span><a href="#">SEARCH</a><span>|</span><a href="#">REPORTS</a><span>|</span><a href="#">ADMIN</a><span>|</span><a href="#">HELP</a></div>
  <div class="copyright">© 2013 Norvale Petrochemical. All Rights Reserved</div>
</footer>
</body>
</html>
```